Flyer Re-Design

We need a flyer re-design for a company that recently started doing it's own graphic design. Although we've taken a first attempt at the design, we would like a design professional, like yourself show us how much better you can do it. We're going through a re-branding as the logo reads "formerly" known as and although we'd like to keep the logo as it is---everything else should be more contemporary.

5.5" x 8.5" or 5" x 7"

Target Market(s)

Bahamas Youth

Industry/Entity Type

Graphic Design

Font styles to use
Sans Serif

Requirements
Must have
• Current Logo. Include as many details as already listed in the document.
Nice to have
• Fresh New, Crisp Ideas for this Pharmacy rebranding
Should not have
• Too Many colors or serif fonts

```html
<!DOCTYPE html>
<html lang="en">
<head>
<meta charset="UTF-8">
<title>Vital Leaf Pharmacy – Rewards Club Flyer</title>
<link rel="stylesheet" href="https://fonts.googleapis.com/css2?family=Fira+Sans:ital,wght@0,400;0,600;0,700;1,400;1,600;1,700&family=Fredoka:wght@500&display=swap">
<style>
  :root {
    --bg: #e6e6e6;
    --paper: #ffffff;
    --green: #2a7a36;
    --green-dark: #1f6b2c;
    --red: #b3191d;
    --ink: #333333;
    --bar: #111111;
    --bar-text: #a8e08a;
  }
  * { box-sizing: border-box; margin: 0; padding: 0; }
  html, body {
    width: 1200px; height: 1000px; overflow: hidden;
    background: var(--bg);
    font-family: "Fira Sans", sans-serif;
  }
  .flyer {
    position: absolute; left: 281px; top: 50px;
    width: 638px; height: 900px;
    background: var(--paper);
    box-shadow: 0 2px 6px rgba(0,0,0,0.12);
    overflow: hidden;
  }
  .flyer > * { position: absolute; }

  .brand { left: 48px; top: 40px; }
  .brand-name {
    display: flex; align-items: center; gap: 8px;
    color: var(--green); font-weight: 700; font-size: 15px; letter-spacing: 0.3px;
  }
  .brand-dot { width: 22px; height: 22px; border-radius: 50%; background: var(--red); }
  .brand-address {
    margin-top: 4px; margin-left: 30px;
    font-size: 7.5px; line-height: 10px; color: var(--ink); text-align: center;
  }

  .photo-hand {
    left: 250px; top: 0; width: 388px; height: 180px;
    background: linear-gradient(200deg, #e0b29e 0%, #eccabb 35%, #f6ece8 65%, #ffffff 100%);
  }
  .photo-apple {
    left: 92px; top: 175px; width: 197px; height: 210px;
    background: radial-gradient(ellipse 48% 45% at 50% 46%, #c8202a 0%, #d9454a 60%, #efc6c4 85%, #ffffff 100%);
  }

  .headline {
    right: 38px; top: 210px;
    font-family: "Fredoka", sans-serif; font-weight: 500;
    font-size: 45px; line-height: 55px; text-align: right;
    color: var(--green); letter-spacing: 0.5px;
  }
  .rule { left: 119px; top: 395px; width: 414px; height: 5px; background: var(--red); }

  .perk {
    top: 434px; width: 108px; height: 108px; border-radius: 50%;
    background: var(--green);
    display: flex; align-items: center; justify-content: center; text-align: center;
    color: #fff; font-style: italic; font-size: 13px; line-height: 16px; padding: 0 18px;
  }
  .perk-1 { left: 47px; } .perk-2 { left: 193px; } .perk-3 { left: 340px; } .perk-4 { left: 484px; }

  .exclusives-title {
    left: 45px; top: 584px;
    color: var(--red); font-weight: 700; font-style: italic; font-size: 40px; letter-spacing: 0.5px;
  }
  .exclusives-list {
    left: 48px; top: 642px; list-style: none;
    font-size: 13px; line-height: 19.5px; color: var(--ink);
  }
  .exclusives-list li::before {
    content: ""; display: inline-block; width: 5px; height: 5px; border-radius: 50%;
    background: #8a8a8a; margin-right: 7px; vertical-align: middle;
  }
  .members-only { color: var(--red); font-weight: 700; font-style: italic; }

  .thanks {
    left: 340px; top: 583px; width: 276px; text-align: center;
    color: var(--green); font-weight: 600; font-style: italic; font-size: 37px; line-height: 45px;
  }
  .thanks-strong { color: var(--red); font-style: normal; font-weight: 700; }
  .visit {
    left: 340px; top: 770px; width: 276px; text-align: center;
    font-size: 9.5px; font-weight: 600; color: var(--ink);
  }
  .visit em { font-style: italic; }

  .cta-bar {
    left: 37px; top: 804px; width: 567px; height: 37px; background: var(--bar);
    display: flex; align-items: center; justify-content: center;
    color: var(--bar-text); font-style: italic; font-weight: 600; font-size: 19px;
  }
  .footer-mark {
    right: 20px; bottom: 12px; display: flex; align-items: center; gap: 5px;
    color: var(--green); font-weight: 700; font-size: 9px;
  }
  .footer-mark .brand-dot { width: 12px; height: 12px; }
</style>
</head>
<body>
  <main class="flyer">
    <div class="photo-hand" role="img" aria-label="Photo of a hand holding a syringe pointed at the apple"></div>
    <div class="photo-apple" role="img" aria-label="Photo of a shiny red apple with a soft reflection"></div>

    <header class="brand">
      <div class="brand-name"><span class="brand-dot"></span>Vital Leaf Pharmacy</div>
      <p class="brand-address">12 Palm Court Drive, Coral Plaza<br>P.O. Box F-0000, Freeport, Grand Bahama, Bahamas<br>Tel: (242) 555 0100 Fax: (242) 555 0101</p>
    </header>

    <h1 class="headline">JOIN OUR<br>REWARDS<br>CLUB NOW!</h1>
    <div class="rule"></div>

    <div class="perk perk-1">Absolutely free to join!</div>
    <div class="perk perk-2">You'll earn 1 point for every Dollar you spend</div>
    <div class="perk perk-3">Earn double points on selected items purchased</div>
    <div class="perk perk-4">Earn 25 points when you refer a friend</div>

    <h2 class="exclusives-title">EXCLUSIVES</h2>
    <ul class="exclusives-list">
      <li>VIP access to our special events.</li>
      <li>Be the first to know about our specials.</li>
      <li>receive notice on non-advertised specials.</li>
      <li>Free subscription to our online newsletter.</li>
      <li>Free gift with sign up.</li>
      <li>Special <span class="members-only">“members only”</span> shopping events</li>
    </ul>

    <p class="thanks">It’s Just<br>Our Way<br>of Saying<br><span class="thanks-strong">THANK YOU.</span></p>
    <p class="visit">visit us at: <em>www.vitalleafpharmacy.com</em></p>

    <div class="cta-bar">See Our Customer Service Representative Today!</div>

    <div class="footer-mark"><span class="brand-dot"></span>Vital Leaf</div>
  </main>
</body>
</html>
```